Web design project for exciting Australian start-up

Background
We are looking for a creative and talented web design artist to work alongside our market leading web developer.
• You will be required to create a modern and clean design theme for our website, incorporating selected rustic colour scheme elements for our exciting Australian start-up to operate within the coffee industry.
reoccurring work to be expected to flow to the successful designer.
Requirements
• c. 5 - 10 page website
• Landing page
• Log in/ out
• 404 template
• Typography is emphasised
• Please use either a) typemarrow.com, b) free web fonts, c) brindle fonts
• All design elements in vector format
• Preferably with icons for each header title(i.e. about us, how it works etc) but designer have free reign over how the site looks, so might not be applicable
• All pages to be responsive
• Down to eSlab resolution

High level visual design brief attached - additional pages to be worked from base design.

Design inspiration
• We would like to use design elements from the following sources:
http://www.zandrix.com/halcyon/ (Functionality)
Colour scheme refer to logo and complementary style guide

```html
<!DOCTYPE html>
<html lang="en">
<head>
<meta charset="utf-8">
<title>Brewhaven – Dashboard</title>
<link rel="stylesheet" href="https://fonts.googleapis.com/css2?family=Arimo:wght@400;700&family=Oswald:wght@400;500&display=swap">
<style>
:root{
  --orange:#d07a1a;
  --orange-dark:#b5630f;
  --red:#ef4548;
  --text:#333;
  --muted:#555;
  --line:#dcdcdc;
  --cell:#f3f3f3;
  --footer:#1d1d1d;
  --footer-head:#e98a2a;
  --footer-link:#c9c9c9;
}
*{box-sizing:border-box;margin:0;padding:0}
html,body{width:1200px;height:795px;overflow:hidden;background:#fff;font-family:"Arimo",Arial,sans-serif;color:var(--text)}
.page{position:relative;width:1200px;height:795px}
.abs{position:absolute}

/* header */
.site-header{position:absolute;left:0;top:0;width:1200px;height:81px;background:linear-gradient(#d9841e,#c26f14 70%,#d58a33);border-bottom:1px solid #e6a25c}
.brand{position:absolute;left:172px;top:24px;display:flex;align-items:center;gap:10px;font-weight:700;font-size:24px;letter-spacing:2px;color:#1c1c1c}
.brand-dot{width:34px;height:34px;border-radius:50%;background:#1c1c1c}
.main-nav a{position:absolute;top:33px;color:#fff;text-decoration:none;font-size:13px}

/* panels */
.panel-head{background:var(--red);color:#fff;font-size:13.5px;height:30px;line-height:30px;padding-left:15px}
.panel{border:1px solid var(--line);border-top:none}
.red-title{color:var(--red);font-size:12.5px}
.small{font-size:9.5px;color:var(--muted);line-height:16px}
.arrows{position:absolute;right:10px;top:0;font-size:14px;letter-spacing:6px}

.photo{width:173px;height:112px;background:radial-gradient(circle at 40% 45%,#e7d7c0 0 18%,#6b3e22 30%,#2f1b10 70%)}

.account-item{padding:10px 16px 9px;border-bottom:1px solid var(--line)}
.account-item:last-child{border-bottom:none}

/* tenders */
.section-title{color:var(--red);font-size:15.5px}
.tender-box{border:1px solid var(--line)}
.tender-head{height:33px;line-height:33px;padding-left:16px;font-size:12.5px;border-bottom:1px solid var(--line)}
.clock{position:absolute;left:18px;top:25px;width:147px;height:48px;border-radius:4px;background:linear-gradient(#eee,#bbb);border:1px solid #999}
.digit{position:absolute;top:8px;width:37px;height:30px;border-radius:3px;background:linear-gradient(#555,#222 50%,#111);color:#fff;font-size:18px;line-height:30px;text-align:center}
.colon{position:absolute;top:13px;font-size:14px;color:#222;font-weight:700}
.clock-label{position:absolute;top:82px;font-size:6.5px;color:#444}
.tender-info{position:absolute;left:188px;top:22px;width:250px;font-size:10px;line-height:20px}
.tender-info .lbl{color:var(--red)}
.tender-info p{font-size:9.5px;line-height:15px;margin-top:4px}

/* table */
.purchases{border-collapse:separate;border-spacing:1px;width:453px}
.purchases th{background:var(--red);color:#fff;font-weight:400;font-size:12.5px;height:33px}
.purchases td{background:var(--cell);font-size:9.5px;text-align:center;height:33px;border-bottom:1px solid #e2e2e2}

/* right */
.inbox-item{font-size:10px;padding:0 0 0 13px;height:29px;line-height:29px;border-bottom:1px solid var(--line)}
.inbox-item:last-child{border-bottom:none}
.delivery{background:#f4f4f4;border:1px solid var(--line);padding:9px 16px;width:165px;height:68px;margin-bottom:2px;white-space:nowrap;overflow:hidden}
.delivery .red-title{font-size:12.5px;margin-bottom:3px}
.scroll{position:absolute;left:166px;top:0;width:6px;height:139px;background:#e2e2e2;border-radius:3px}
.scroll i{position:absolute;left:1px;top:4px;width:4px;height:24px;background:#999;border-radius:2px}

.calendar{border:1px solid #d8d8d8;border-radius:5px;background:#fafafa}
.cal-title{position:absolute;left:0;top:10px;width:100%;text-align:center;font-size:10.5px;color:#333}
.cal-title b{color:var(--red)}
.cal-nav{position:absolute;top:10px;font-size:9px;color:#555}
.cal-grid{position:absolute;left:11px;top:37px;display:grid;grid-template-columns:repeat(7,20.5px);column-gap:1.8px;row-gap:1.5px}
.cal-grid span{height:16.5px;font-size:8.5px;text-align:center;line-height:16px;border:1px solid #ddd;background:#fff}
.cal-grid .dow{border:none;background:none;color:#666;font-size:9px}
.cal-grid .off{color:#bbb}
.cal-grid .today{background:#666;color:#fff;border-color:#666}
.cal-grid .bold{font-weight:700}

.download{font-size:10.5px;font-weight:700;color:var(--red);display:flex;align-items:center;gap:8px}

/* footer */
.site-footer{position:absolute;left:0;top:633px;width:1200px;height:162px;background:repeating-linear-gradient(45deg,#222 0 2px,#1a1a1a 2px 4px)}
.footer-col{position:absolute;top:26px}
.footer-col h3{font-family:"Oswald",sans-serif;font-weight:500;font-size:17px;color:var(--footer-head);margin-bottom:6px;letter-spacing:.3px}
.footer-col a{display:block;color:var(--footer-link);font-size:10.5px;text-decoration:none;line-height:20.6px;padding-left:2px}
.footer-brand{position:absolute;left:777px;top:34px;display:flex;align-items:center;gap:8px;font-weight:700;font-size:17px;letter-spacing:2px;color:#8a8a8a}
.footer-brand span.dot{width:26px;height:26px;border-radius:50%;background:#8a8a8a}
.copyright{position:absolute;left:783px;top:78px;font-size:10.5px;line-height:20.6px;color:var(--footer-link)}
</style>
</head>
<body>
<div class="page">

<header class="site-header">
  <div class="brand"><span class="brand-dot"></span>BREWHAVEN</div>
  <nav class="main-nav">
    <a style="left:617px">Login</a>
    <a style="left:702px">Helpful info</a>
    <a style="left:820px">How we are</a>
    <a style="left:941px">Join us now</a>
  </nav>
</header>

<section class="abs" style="left:172px;top:106px;width:173px">
  <div class="panel-head" style="position:relative">Photos<span class="arrows">‹›</span></div>
  <div class="photo" role="img" aria-label="Cup of coffee beside a sack of roasted beans"></div>
  <div class="panel" style="padding:14px 16px 12px;height:76px">
    <div class="red-title">Café Marlowe</div>
    <div class="small">Melbourne, Australia<br>Member since [Feb, 2014]</div>
  </div>
</section>

<section class="abs" style="left:172px;top:345px;width:173px">
  <div class="panel-head">My account</div>
  <div class="panel">
    <div class="account-item"><div class="red-title">Email Address</div><div class="small">Verified</div></div>
    <div class="account-item"><div class="red-title">Café type</div><div class="small">(i.e. Café, speciality coffee shop, restaurant)</div></div>
    <div class="account-item"><div class="red-title">Payment details</div><div class="small">Verified</div></div>
  </div>
</section>

<h2 class="abs section-title" style="left:374px;top:113px;font-weight:400">Live Tenders</h2>
<section class="abs tender-box" style="left:374px;top:142px;width:452px;height:146px">
  <div class="tender-head">Time remaining</div>
  <div class="abs" style="left:0;top:33px;width:450px;height:110px">
    <div class="clock">
      <div class="digit" style="left:8px">05</div><span class="colon" style="left:48px">:</span>
      <div class="digit" style="left:54px">24</div><span class="colon" style="left:94px">:</span>
      <div class="digit" style="left:100px">36</div>
    </div>
    <span class="clock-label" style="left:35px">Hours</span>
    <span class="clock-label" style="left:78px">Minutes</span>
    <span class="clock-label" style="left:123px">Seconds</span>
    <div class="tender-info">
      <div><span class="lbl">Quantity (kg) :</span> 35 kg/week</div>
      <div><span class="lbl">Café type :</span> Speciality coffee shop</div>
      <p>will uncover many web sites still in their infancy. Various versions have evolved...</p>
    </div>
  </div>
</section>

<h2 class="abs section-title" style="left:374px;top:307px;font-weight:400">Purchases</h2>
<table class="abs purchases" style="left:373px;top:335px">
  <thead><tr><th style="width:130px">All</th><th style="width:161px">Period (x months)</th><th>Awaiting feedback (x)</th></tr></thead>
  <tbody>
    <tr><td>Speciality coffee shop</td><td>25 Dec 2014</td><td>Good Deliverables</td></tr>
    <tr><td>Speciality coffee shop</td><td>25 Dec 2014</td><td>Good Deliverables</td></tr>
    <tr><td>Speciality coffee shop</td><td>25 Dec 2014</td><td>Good Deliverables</td></tr>
    <tr><td>Speciality coffee shop</td><td>25 Dec 2014</td><td>Good Deliverables</td></tr>
    <tr><td>Speciality coffee shop</td><td>25 Dec 2014</td><td>Good Deliverables</td></tr>
    <tr><td>Speciality coffee shop</td><td>25 Dec 2014</td><td>Good Deliverables</td></tr>
  </tbody>
</table>

<section class="abs" style="left:856px;top:106px;width:173px">
  <div class="panel-head">Inbox</div>
  <div class="panel">
    <div class="inbox-item">›&nbsp; Messages</div>
    <div class="inbox-item">›&nbsp; Saved searches</div>
  </div>
</section>

<h2 class="abs section-title" style="left:856px;top:215px;font-weight:400;font-size:13px;line-height:20.5px">Incoming deliveries<br>this week</h2>
<span class="abs" style="left:1005px;top:228px;font-size:14px;color:#777;letter-spacing:6px">‹›</span>

<section class="abs" style="left:856px;top:260px;width:173px">
  <div class="delivery"><div class="red-title">8 am – 11 am</div><div class="small">Delivery of order 3220x<br>Order: 20kg Kestrel Beans</div></div>
  <div class="delivery"><div class="red-title">11 am – 3 pm</div><div class="small">Delivery of order 3221y<br>Order: Sample testing Corvallo</div></div>
  <div class="scroll"><i></i></div>
</section>

<section class="abs calendar" style="left:856px;top:414px;width:175px;height:168px">
  <span class="cal-nav" style="left:18px">«</span>
  <div class="cal-title">February <b>2014</b></div>
  <span class="cal-nav" style="right:18px">»</span>
  <div class="cal-grid">
    <span class="dow">Su</span><span class="dow">Mo</span><span class="dow">Tu</span><span class="dow">We</span><span class="dow">Th</span><span class="dow">Fr</span><span class="dow">Sa</span>
    <span class="off">25</span><span class="off">26</span><span class="off">27</span><span class="off">28</span><span class="off">29</span><span class="off">30</span><span>1</span>
    <span>2</span><span>3</span><span>4</span><span>5</span><span>6</span><span>7</span><span>8</span>
    <span>9</span><span>10</span><span>11</span><span>12</span><span>13</span><span class="bold">14</span><span>15</span>
    <span>16</span><span>17</span><span>18</span><span>19</span><span>20</span><span class="today">21</span><span>22</span>
    <span>23</span><span>24</span><span>25</span><span>26</span><span>27</span><span>28</span><span>29</span>
    <span>30</span><span class="off">1</span><span class="off">2</span><span class="off">3</span><span class="off">4</span><span class="off">5</span><span class="off">6</span>
  </div>
</section>

<a class="abs download" style="left:864px;top:591px">
  <svg width="16" height="16" viewBox="0 0 16 16" aria-hidden="true"><path d="M8 2v8M4.5 6.5L8 10l3.5-3.5" fill="none" stroke="#ef4548" stroke-width="1.8" stroke-linecap="round" stroke-linejoin="round"/><path d="M2 11v3h12v-3" fill="none" stroke="#ef4548" stroke-width="1.8" stroke-linecap="round" stroke-linejoin="round"/></svg>
  Download
</a>

<footer class="site-footer">
  <div class="footer-col" style="left:173px"><h3>HELPFUL INFO</h3><a>About us</a><a>Media enquiries</a><a>Terms &amp; conditions</a><a>Privacy policy</a></div>
  <div class="footer-col" style="left:387px"><h3>WHO WE ARE</h3><a>How it works</a><a>FAQ</a><a>Contact us</a></div>
  <div class="footer-col" style="left:584px"><h3>JOIN US ON</h3><a>Friendloop</a><a>Chirpline</a><a>Workgrid</a><a>Viewcast</a></div>
  <div class="footer-brand"><span class="dot"></span>BREWHAVEN</div>
  <div class="copyright">Copyright © 2014 Brewhaven.<br>All rights reserved.</div>
</footer>

</div>
</body>
</html>
```